Business Card Design

We are looking for a business card designed for our landscaping company. We do landscaping installation & Maintenance Services. We would like to see designs that have basic landscaping in background. We also think it is important to have both of our names and phone numbers on the card. We need something that stands out a little whether it is shape of the card or thickness or design.

Business

Bramblewood Yardworks, bramblewoodyard@mailvista.net, Owen Platt 555-273-9104, Daniel Korbin 555-618-3927

```html
<!DOCTYPE html>
<html lang="en">
<head>
<meta charset="utf-8">
<title>Bramblewood Yardworks – Business Card</title>
<link rel="stylesheet" href="https://fonts.googleapis.com/css2?family=Old+Standard+TT:wght@700&family=Arimo:wght@400&display=swap">
<style>
  :root {
    --page-bg: #ecebe8;
    --leaf-light: #d8f5cf;
    --leaf-mid: #a6e698;
    --stripe-green: #3cd41c;
    --ink-black: #000000;
    --ink-white: #ffffff;
    --shadow: rgba(0, 0, 0, 0.35);
  }
  * { margin: 0; padding: 0; box-sizing: border-box; }
  html, body {
    width: 1189px;
    height: 1200px;
    overflow: hidden;
    background: var(--page-bg);
  }
  .card {
    position: absolute;
    left: 44px;
    top: 286px;
    width: 1100px;
    height: 628px;
    box-shadow: 4px 6px 14px var(--shadow);
    overflow: hidden;
  }
  .card__top {
    position: absolute;
    left: 0; top: 0;
    width: 100%;
    height: 338px;
    background: linear-gradient(180deg, var(--leaf-mid) 0%, #bdedb0 45%, var(--leaf-light) 100%);
  }
  .card__foliage {
    position: absolute;
    left: 0; top: 0;
    width: 320px;
    height: 200px;
    background: radial-gradient(ellipse at 25% 20%, rgba(120, 190, 110, 0.45) 0%, rgba(120, 190, 110, 0) 70%);
  }
  .card__stripe {
    position: absolute;
    left: 0; top: 338px;
    width: 100%;
    height: 23px;
    background: var(--stripe-green);
  }
  .card__bottom {
    position: absolute;
    left: 0; top: 361px;
    width: 100%;
    height: 267px;
    background: var(--ink-black);
  }
  .card__foliage--dark {
    position: absolute;
    right: 0; bottom: 0;
    width: 460px;
    height: 240px;
    background: radial-gradient(ellipse at 70% 70%, rgba(40, 40, 40, 0.7) 0%, rgba(0, 0, 0, 0) 70%);
  }
  .company-name {
    position: absolute;
    left: 0; top: 128px;
    width: 100%;
    text-align: center;
    font-family: "Old Standard TT", "Century Schoolbook", serif;
    font-weight: 700;
    font-size: 60px;
    line-height: 1;
    color: var(--ink-black);
  }
  .company-email {
    position: absolute;
    left: 0; top: 262px;
    width: 100%;
    text-align: center;
    font-family: "Arimo", Arial, sans-serif;
    font-size: 32px;
    line-height: 1;
    color: var(--ink-black);
  }
  .divider {
    position: absolute;
    left: 541px; top: 64px;
    width: 2px;
    height: 132px;
    background: var(--ink-white);
  }
  .contact {
    position: absolute;
    top: 76px;
    color: var(--ink-white);
  }
  .contact--left { right: 672px; text-align: right; }
  .contact--right { left: 646px; text-align: left; }
  .contact__name {
    font-family: "Old Standard TT", "Century Schoolbook", serif;
    font-weight: 700;
    font-size: 42px;
    line-height: 48px;
  }
  .contact__phone {
    font-family: "Arimo", Arial, sans-serif;
    font-size: 32px;
    line-height: 44px;
  }
</style>
</head>
<body>
  <div class="card">
    <div class="card__top">
      <div class="card__foliage" role="img" aria-label="Faint bamboo leaf sprigs in the corner"></div>
      <div class="company-name">Bramblewood Yardworks</div>
      <div class="company-email">bramblewoodyard@mailvista.net</div>
    </div>
    <div class="card__stripe"></div>
    <div class="card__bottom">
      <div class="card__foliage--dark" role="img" aria-label="Faint dark bamboo leaves in the corner"></div>
      <div class="contact contact--left">
        <div class="contact__name">Owen Platt</div>
        <div class="contact__phone">555-273-9104</div>
      </div>
      <div class="divider"></div>
      <div class="contact contact--right">
        <div class="contact__name">Daniel Korbin</div>
        <div class="contact__phone">555-618-3927</div>
      </div>
    </div>
  </div>
</body>
</html>
```